Namibia currently imports 60% of its food. Harvest Crest Oruva is an initiative which will assist Namibia to become self sustainable in terms of food production. We aim to do this through the development of 3 agricultural production zones which will include farming zones, local farmer assistance, processing and distribution of the final products. Please see our project overview attached.

```html
<!DOCTYPE html>
<html lang="en">
<head>
<meta charset="utf-8">
<title>Harvest Crest Oruva</title>
<link href="https://fonts.googleapis.com/css2?family=Cinzel:wght@400;500&family=Poppins:wght@400;500;600&display=swap" rel="stylesheet">
<style>
:root{
  --green:#0b6b36;
  --green-dark:#07552a;
  --beige:#c9a27f;
  --blue:#2ba6df;
  --grey:#efefef;
  --ink:#1d1d1d;
  --muted:#555;
  --footer:#121212;
  --white:#fff;
}
*{box-sizing:border-box;margin:0;padding:0}
html,body{width:1200px;height:5254px;overflow:hidden}
body{font-family:"Poppins",sans-serif;color:var(--ink);background:var(--white);position:relative}
.abs{position:absolute}
section,header,footer,.band{position:absolute;left:0;width:1200px}
.serif{font-family:"Cinzel",serif;font-weight:400}
.btn{position:absolute;display:flex;align-items:center;justify-content:center;background:var(--green);color:#fff;font-size:12px;font-weight:500;border-radius:3px}
.sec-title{position:absolute;left:0;width:1200px;text-align:center;font-family:"Cinzel",serif;font-size:38px;color:var(--ink);letter-spacing:1px}
.sec-lead{position:absolute;left:150px;width:900px;text-align:center;font-size:12.5px;line-height:22px;color:#333}
.photo{position:absolute}

/* top bar */
.topbar{top:0;height:29px;background:var(--green);color:#fff;font-size:12px}
.topbar .social{position:absolute;left:141px;top:8px;display:flex;gap:8px}
.topbar .social span{width:12px;height:12px;border-radius:50%;background:#fff;display:block}
.topbar .contact{position:absolute;right:141px;top:6px;display:flex;gap:22px;align-items:center}
.topbar .contact div{display:flex;gap:6px;align-items:center}

/* header */
.site-header{top:29px;height:73px;background:#fff}
.brand{position:absolute;left:141px;top:22px;font-family:"Cinzel",serif;font-size:24px;color:var(--green)}
.nav{position:absolute;top:31px;font-size:12px;font-weight:500}
.nav-contact{left:951px;top:22px;width:106px;height:37px;border-radius:20px;font-weight:600}

/* hero */
.hero{top:102px;height:488px;background:linear-gradient(100deg,#3b3a1d 0%,#6a6b2e 40%,#8a7b3a 65%,#4a4a22 100%)}
.hero h1{position:absolute;left:141px;top:150px;font-size:35px;line-height:50px;font-weight:600;color:#fff}
.hero p{position:absolute;left:141px;top:270px;font-size:13px;color:#fff}
.hero .cta{position:absolute;left:141px;top:316px;width:222px;height:36px;border-radius:20px;background:var(--beige);color:#fff;font-size:12px;font-weight:500;display:flex;align-items:center;justify-content:center;gap:8px}
.down{position:absolute;left:563px;top:553px;width:74px;height:74px;border-radius:50%;background:#fff;display:flex;align-items:center;justify-content:center;z-index:2}

/* pillars */
.pillars{top:649px;height:324px;background:var(--grey)}
.pillar{position:absolute;top:45px;width:304px;height:222px;background:#fff;padding:36px 30px}
.pillar h3{font-family:"Cinzel",serif;font-weight:400;font-size:17px;margin-top:18px;letter-spacing:.5px}
.pillar p{font-size:12px;line-height:22px;color:#444;margin-top:8px}

/* about */
.about{top:973px;height:665px}
.about-text{position:absolute;left:618px;top:266px;width:430px;font-size:12px;line-height:22px;color:#333}
.about-text p{margin-bottom:10px}

/* projects */
.projects{top:1638px;height:729px;background:var(--grey)}
.card{position:absolute;background:#fff}
.card h4{font-family:"Cinzel",serif;font-weight:400;font-size:17px;line-height:22px;letter-spacing:.5px}
.card p{font-size:12px;line-height:22px;color:#444}
.card a{font-size:11.5px;font-weight:600;color:var(--green);text-decoration:underline}
.arrow{position:absolute;width:38px;height:38px;border-radius:50%;background:#fff;box-shadow:0 1px 4px rgba(0,0,0,.2);display:flex;align-items:center;justify-content:center}

/* reviews */
.reviews{top:2367px;height:422px}
.reviews .panel{position:absolute;left:600px;top:0;width:600px;height:422px;background:var(--green);color:#fff}
.reviews h2{position:absolute;left:57px;top:112px;font-family:"Cinzel",serif;font-weight:400;font-size:34px;letter-spacing:1px}
.reviews blockquote{position:absolute;left:57px;top:166px;width:410px;font-size:12px;line-height:23px}
.reviewer{position:absolute;left:57px;top:295px;display:flex;gap:12px;align-items:center}
.avatar{width:46px;height:46px;border-radius:50%;background:#d9c3a4}

/* zones */
.zones{top:2789px;height:581px}
.zones h2{position:absolute;left:141px;top:138px;font-family:"Cinzel",serif;font-weight:400;font-size:34px;line-height:38px;letter-spacing:1px}
.zones .desc{position:absolute;left:141px;top:220px;width:440px;font-size:12px;line-height:23px;color:#333}
.legend{position:absolute;left:141px;display:flex;gap:12px;align-items:center;font-size:14px;font-weight:500}
.legend i{width:18px;height:18px;display:block}

/* stats */
.stats{top:3370px;height:335px}
.stat{position:absolute;top:0;width:396px;height:335px;color:#fff;text-align:center}
.stat .num{position:absolute;left:0;width:100%;top:92px;font-size:94px;font-weight:600;color:rgba(255,255,255,.82);letter-spacing:2px}
.stat .lbl{position:absolute;left:0;width:100%;top:214px;font-size:19px;font-weight:500}

/* news */
.news{top:3705px;height:801px}
.news .date{font-size:11.5px;color:#666}
.news h5{font-size:13px;font-weight:600;line-height:22px;margin-top:12px}
.news p{font-size:11.5px;line-height:22px;color:#555;margin-top:10px}
.news a{display:block;margin-top:12px;font-size:11.5px;font-weight:600;color:var(--green);text-decoration:underline}
.news .card{border:1px solid #e3e3e3}

/* newsletter */
.newsletter{position:absolute;left:141px;top:4504px;width:918px;height:317px;background:linear-gradient(90deg,#0d5b2c 0%,#137a3a 55%,#3d9b35 80%,#a9c83a 100%);color:#fff}
.newsletter h2{position:absolute;left:72px;top:86px;font-family:"Cinzel",serif;font-weight:400;font-size:34px;letter-spacing:1px}
.newsletter p{position:absolute;left:72px;top:140px;width:420px;font-size:12px;line-height:23px}
.newsletter .input{position:absolute;left:72px;top:201px;width:308px;height:41px;background:#fff;color:#222;font-size:12px;font-weight:500;padding:12px 22px}
.newsletter .sub{position:absolute;left:387px;top:201px;width:125px;height:41px;background:var(--beige);color:#fff;font-size:12px;display:flex;align-items:center;justify-content:center}

/* footer */
.site-footer{top:4906px;height:302px;background:var(--footer);color:#fff}
.site-footer h6{position:absolute;font-family:"Cinzel",serif;font-weight:400;font-size:18px;letter-spacing:1px}
.links{position:absolute;left:141px;top:94px;list-style:none;font-size:12px;line-height:28.6px;font-weight:500}
.footer-brand{position:absolute;left:424px;top:110px;width:250px;text-align:center;font-family:"Cinzel",serif;font-size:30px;line-height:40px;color:var(--green)}
.ci{position:absolute;left:822px;display:flex;gap:14px;font-size:12px;line-height:20px}
.ci .ico{width:26px;height:26px;border-radius:4px;background:#3a3a3a;display:flex;align-items:center;justify-content:center;flex:none}
.bottombar{top:5208px;height:46px;background:var(--green);color:#fff;font-size:12px}
.bottombar .social{position:absolute;right:141px;top:17px;display:flex;gap:8px}
.bottombar .social span{width:12px;height:12px;border-radius:50%;background:#fff;display:block}
</style>
</head>
<body>

<div class="band topbar">
  <div class="social"><span></span><span></span><span></span><span></span></div>
  <div class="contact">
    <div><svg width="14" height="11" viewBox="0 0 14 11"><rect x="1" y="1" width="12" height="9" fill="none" stroke="#fff" stroke-width="1.3"/><path d="M1 1l6 5 6-5" fill="none" stroke="#fff" stroke-width="1.3"/></svg>info@harvestcrestoruva.com</div>
    <div><svg width="12" height="12" viewBox="0 0 24 24"><path d="M6.6 10.8a15 15 0 006.6 6.6l2.2-2.2c.3-.3.7-.4 1-.2 1.1.4 2.3.6 3.6.6.6 0 1 .4 1 1V20c0 .6-.4 1-1 1A17 17 0 013 4c0-.6.4-1 1-1h3.5c.6 0 1 .4 1 1 0 1.3.2 2.5.6 3.6.1.3 0 .7-.2 1z" fill="none" stroke="#fff" stroke-width="2"/></svg>123-456-7890</div>
  </div>
</div>

<header class="site-header">
  <div class="brand">Harvest Crest Oruva</div>
  <div class="nav" style="left:492px">About Us</div>
  <div class="nav" style="left:580px">Our Projects</div>
  <div class="nav" style="left:686px">Farmer Resources</div>
  <div class="nav" style="left:822px">News &amp; Updates</div>
  <div class="btn nav-contact">Contact Us</div>
</header>

<section class="hero">
  <div class="photo" style="inset:0" role="img" aria-label="Farmers working in a sunlit field of crops"></div>
  <h1>Empowering Namibia To<br>Achieve Food Independence.</h1>
  <p>Reducing imports by fostering local agricultural production.</p>
  <div class="cta">Learn About Our Projects <svg width="16" height="10" viewBox="0 0 16 10"><path d="M0 5h14M10 1l4 4-4 4" fill="none" stroke="#fff" stroke-width="1.4"/></svg></div>
</section>
<div class="down"><svg width="34" height="34" viewBox="0 0 34 34"><rect x="9" y="2" width="16" height="30" rx="8" fill="none" stroke="#0b6b36" stroke-width="2"/><path d="M17 9v14M12 18l5 5 5-5" fill="none" stroke="#0b6b36" stroke-width="2"/></svg></div>

<section class="pillars">
  <div class="pillar" style="left:141px">
    <svg width="40" height="40" viewBox="0 0 40 40" fill="none" stroke="#333" stroke-width="2"><circle cx="19" cy="21" r="15"/><circle cx="19" cy="21" r="9"/><circle cx="19" cy="21" r="3"/><path d="M19 21L34 6M29 6h5v5"/></svg>
    <h3>OUR MISSION</h3>
    <p>Lorem ipsum dolor sit amet, dolor ex consectetur adipiscing elit, sed do ut eiusmod tempor.</p>
  </div>
  <div class="pillar" style="left:447px">
    <svg width="40" height="40" viewBox="0 0 40 40" fill="none" stroke="#333" stroke-width="2"><circle cx="20" cy="10" r="6"/><circle cx="9" cy="22" r="4"/><circle cx="31" cy="22" r="4"/><path d="M3 36c0-5 3-8 6-8s6 3 6 8M25 36c0-5 3-8 6-8s6 3 6 8M12 24c1-4 4-6 8-6s7 2 8 6"/></svg>
    <h3>OUR VISION</h3>
    <p>Lorem ipsum dolor sit amet, dolor ex consectetur adipiscing elit, sed do ut eiusmod tempor.</p>
  </div>
  <div class="pillar" style="left:753px">
    <svg width="40" height="40" viewBox="0 0 40 40" fill="none" stroke="#333" stroke-width="2"><circle cx="20" cy="16" r="7"/><path d="M20 13v6M17 16h6M4 20v8l8 8h6M36 20v8l-8 8h-6M8 6l2 3M32 6l-2 3M20 2v4"/></svg>
    <h3>OUR VALUES</h3>
    <p>Lorem ipsum dolor sit amet, dolor ex consectetur adipiscing elit, sed do ut eiusmod tempor.</p>
  </div>
</section>

<section class="about">
  <h2 class="sec-title" style="top:104px">ABOUT US</h2>
  <p class="sec-lead" style="top:157px">Lorem ipsum dolor sit amet, consectetur adipiscing elit, sed do eiusmod tempor incididunt ut labore et dolore magna aliqua. Ut enim ad minim veniam, quis nostrud exercitation ullamco laboris nisi ut aliquip ex ea commodo consequat.</p>
  <div class="photo" style="left:141px;top:229px;width:414px;height:353px;background:linear-gradient(180deg,#4f8a2b 0%,#3d6b22 35%,#6b4a2c 60%,#8a6a44 100%)" role="img" aria-label="Freshly harvested potatoes on soil with green crop rows behind"></div>
  <div class="about-text">
    <p>Lorem Ipsum is simply dummy text of the printing and typesetting industry. Lorem Ipsum has been the industry's standard dummy text ever since the 1500s, when an unknown printer took a galley of type and scrambled it to make a type specimen book.</p>
    <p>It is a long established fact that a reader will be distracted by the readable content of a page when looking at its layout.</p>
    <p>Lorem ipsum dolor sit amet, consectetur adipiscing elit, sed do eiusmod tempor incididunt ut labore et dolore magna aliqua.</p>
  </div>
  <div class="btn" style="left:618px;top:494px;width:127px;height:41px">Read More</div>
</section>

<section class="projects">
  <h2 class="sec-title" style="top:106px">OUR PROJECTS</h2>
  <p class="sec-lead" style="top:157px">Ut enim ad minim veniam, quis nostrud exercitation ullamco laboris nisi ut aliquip ex ea commodo consequat.</p>
  <div class="card" style="left:141px;top:206px;width:289px;height:370px">
    <div class="photo" style="left:0;top:0;width:289px;height:186px;background:linear-gradient(180deg,#6f9fd6 0%,#a9c6e4 30%,#5f8f3a 45%,#7aa44a 100%)" role="img" aria-label="Wide green crop field with a farm building on the horizon"></div>
    <div class="abs" style="left:20px;top:208px;width:250px"><h4>AGRICULTURAL PRODUCTION ZONES</h4><p style="margin-top:14px">Lorem Ipsum is simply dummy text of the printing and typesetting industry.</p><a style="display:block;margin-top:18px">Read More</a></div>
  </div>
  <div class="card" style="left:455px;top:206px;width:290px;height:370px">
    <div class="photo" style="left:0;top:0;width:290px;height:186px;background:linear-gradient(180deg,#4f7a2e 0%,#7fa556 50%,#3f6a25 100%)" role="img" aria-label="Farmer using a tablet among tall green plants"></div>
    <div class="abs" style="left:20px;top:208px;width:250px"><h4>LOCAL FARMER ASSISTANCE</h4><p style="margin-top:14px">Lorem Ipsum is simply dummy text of the printing and typesetting industry.</p><a style="display:block;margin-top:18px">Read More</a></div>
  </div>
  <div class="card" style="left:769px;top:206px;width:290px;height:370px">
    <div class="photo" style="left:0;top:0;width:290px;height:186px;background:linear-gradient(180deg,#7fa7d4 0%,#3b5a8a 40%,#a8503a 70%,#6b5a3a 100%)" role="img" aria-label="Workers loading crates of produce beside a tractor"></div>
    <div class="abs" style="left:20px;top:208px;width:250px"><h4>PROCESSING AND DISTRIBUTION</h4><p style="margin-top:14px">Lorem Ipsum is simply dummy text of the printing and typesetting industry.</p><a style="display:block;margin-top:18px">Read More</a></div>
  </div>
  <div class="arrow" style="left:75px;top:372px"><svg width="12" height="12" viewBox="0 0 12 12"><path d="M8 1L3 6l5 5" fill="none" stroke="#111" stroke-width="2"/></svg></div>
  <div class="arrow" style="left:1085px;top:372px"><svg width="12" height="12" viewBox="0 0 12 12"><path d="M4 1l5 5-5 5" fill="none" stroke="#111" stroke-width="2"/></svg></div>
  <div class="btn" style="left:537px;top:604px;width:126px;height:43px">Contact Us</div>
</section>

<section class="reviews">
  <div class="photo" style="left:0;top:0;width:600px;height:422px;background:linear-gradient(160deg,#5a7a2e 0%,#8a7a3a 40%,#6a4a2a 70%,#4a3a22 100%)" role="img" aria-label="Women tending crops in a field with hoes"></div>
  <div class="panel">
    <h2>CUSTOMER REVIEWS</h2>
    <blockquote>"Sed ut perspiciatis unde omnis iste natus error sit voluptatem accusantium doloremque laudantium, totam rem aperiam, ex eaque ipsa quae ab illo inventore veritatis et quasi architecto beatae vitae dicta sunt explicabo. Nemo enim ipsam."</blockquote>
    <div class="reviewer">
      <div class="avatar" role="img" aria-label="Reviewer portrait"></div>
      <div><div style="font-size:13px;font-weight:600">Tomas Kerren</div>
        <svg width="90" height="14" viewBox="0 0 90 14"><g fill="#f2b61f"><path id="s" d="M7 0l2 4.6 5 .5-3.8 3.3 1.1 5L7 10.8 2.7 13.4l1.1-5L0 5.1l5-.5z"/><use href="#s" x="18"/><use href="#s" x="36"/><use href="#s" x="54"/><use href="#s" x="72"/></g></svg>
      </div>
    </div>
  </div>
</section>

<section class="zones">
  <h2>AGRICULTURAL<br>PRODUCTION ZONES</h2>
  <p class="desc">Ut enim ad minim veniam, quis nostrud exercitation ullamco laboris nisi ut aliquip ex ea commodo consequat.</p>
  <div class="legend" style="top:297px"><i style="background:var(--green)"></i>Farming Zones</div>
  <div class="legend" style="top:342px"><i style="background:var(--beige)"></i>Local Farmer Assistance</div>
  <div class="legend" style="top:389px"><i style="background:var(--blue)"></i>Processing and Distribution</div>
  <div class="btn" style="left:141px;top:427px;width:126px;height:44px">Contact Us</div>
  <div class="photo" style="left:661px;top:88px;width:400px;height:408px;background:linear-gradient(170deg,#0b6b36 0%,#2ba6df 40%,#c9a27f 55%,#0b6b36 80%);border-radius:6px" role="img" aria-label="Map of Namibia divided into farming, farmer assistance and processing regions"></div>
</section>

<section class="stats">
  <div class="stat" style="left:0;background:linear-gradient(180deg,#1f4fa0 0%,#3a7ad0 45%,#2f6a2a 75%,#3f8a2f 100%)" role="img" aria-label="Green field under blue sky">
    <div class="num">75%</div><div class="lbl">Hectares Of Land Cultivated</div></div>
  <div class="stat" style="left:402px;background:linear-gradient(180deg,#3f7a3f 0%,#5a9a4f 50%,#2f5a2a 100%)" role="img" aria-label="Farmer among green plants">
    <div class="num">25%</div><div class="lbl">Farmers Assisted</div></div>
  <div class="stat" style="left:804px;background:linear-gradient(180deg,#7a8a8a 0%,#5a6a5a 50%,#3f6a2f 100%)" role="img" aria-label="Grain silos beside a field">
    <div class="num">85%</div><div class="lbl">Reduction In Food Imports</div></div>
</section>

<section class="news">
  <h2 class="sec-title" style="top:101px">LATEST NEWS AND UPDATES</h2>
  <p class="sec-lead" style="top:153px">Lorem ipsum dolor sit amet, consectetur adipiscing elit, sed do eiusmod tempor incididunt ut labore et dolore magna aliqua.</p>
  <div class="card" style="left:141px;top:204px;width:289px;height:437px">
    <div class="photo" style="left:0;top:0;width:287px;height:206px;background:linear-gradient(180deg,#5f8a3a 0%,#7aa04a 50%,#4a6a2a 100%)" role="img" aria-label="Farmer bending over rows of leafy crops"></div>
    <div class="abs" style="left:29px;top:230px;width:235px"><div class="date">10, June 2024</div><h5>Lorem ipsum dolor sit ametco adipiscing eliter sed diam</h5><p>Lorem ipsum dolor sit ametewroe ctetuer adipiscing eliter sed diam utlaoreetere sed diam</p><a>Read More</a></div>
  </div>
  <div class="card" style="left:455px;top:204px;width:290px;height:437px">
    <div class="abs" style="left:29px;top:24px;width:235px"><div class="date">28, May 2024</div><h5>Lorem ipsum dolor sit ametco adipiscing eliter sed diam</h5><p>Lorem ipsum dolor sit ametewroe ctetuer adipiscing eliter sed diam utlaoreetere sed diam</p><a>Read More</a></div>
    <div class="photo" style="left:0;top:231px;width:288px;height:204px;background:linear-gradient(180deg,#6f9fd6 0%,#a9c6e4 30%,#5f8f3a 45%,#7aa44a 100%)" role="img" aria-label="Green crop field with farm buildings"></div>
  </div>
  <div class="card" style="left:769px;top:204px;width:290px;height:437px">
    <div class="photo" style="left:0;top:0;width:288px;height:206px;background:linear-gradient(180deg,#5a7a3a 0%,#c99a3a 50%,#4a5a2a 100%)" role="img" aria-label="Two farmers holding a basket of harvest in a maize field"></div>
    <div class="abs" style="left:29px;top:230px;width:235px"><div class="date">14, April 2024</div><h5>Lorem ipsum dolor sit ametco adipiscing eliter sed diam</h5><p>Lorem ipsum dolor sit ametewroe ctetuer adipiscing eliter sed diam utlaoreetere sed diam</p><a>Read More</a></div>
  </div>
  <div class="arrow" style="left:75px;top:403px"><svg width="12" height="12" viewBox="0 0 12 12"><path d="M8 1L3 6l5 5" fill="none" stroke="#111" stroke-width="2"/></svg></div>
  <div class="arrow" style="left:1085px;top:403px"><svg width="12" height="12" viewBox="0 0 12 12"><path d="M4 1l5 5-5 5" fill="none" stroke="#111" stroke-width="2"/></svg></div>
  <div class="btn" style="left:490px;top:673px;width:220px;height:42px">View All News And Updates</div>
</section>

<div class="newsletter" role="img" aria-label="Green crop field background with a leaf and droplet illustration">
  <h2>NEWSLETTER SIGN UP</h2>
  <p>Sed ut perspiciatis unde omnis iste natus error sit voluptatem accusantium doloremque laudantium, totam rem aperiam.</p>
  <div class="input">Enter Your Email Address</div>
  <div class="sub">Subscribe</div>
</div>

<footer class="site-footer">
  <h6 style="left:141px;top:58px">QUICK LINKS</h6>
  <ul class="links">
    <li>• Home</li><li>• About Us</li><li>• Our Projects</li><li>• Farmer Resources</li><li>• News &amp; Updates</li><li>• Contact Us</li>
  </ul>
  <div class="footer-brand">Harvest Crest<br>Oruva</div>
  <h6 style="left:822px;top:58px">CONTACT DETAILS</h6>
  <div class="ci" style="top:96px"><div class="ico"><svg width="12" height="14" viewBox="0 0 12 14"><path d="M6 13s5-5 5-8A5 5 0 001 5c0 3 5 8 5 8z" fill="#fff"/><circle cx="6" cy="5" r="1.8" fill="#3a3a3a"/></svg></div><div>123, Building Name, Street City,<br>State XY 123456</div></div>
  <div class="ci" style="top:156px"><div class="ico"><svg width="13" height="10" viewBox="0 0 14 11"><rect x="1" y="1" width="12" height="9" fill="none" stroke="#fff" stroke-width="1.3"/><path d="M1 1l6 5 6-5" fill="none" stroke="#fff" stroke-width="1.3"/></svg></div><div>Email<br>info@harvestcrestoruva.com</div></div>
  <div class="ci" style="top:216px"><div class="ico"><svg width="12" height="12" viewBox="0 0 24 24"><path d="M6.6 10.8a15 15 0 006.6 6.6l2.2-2.2c.3-.3.7-.4 1-.2 1.1.4 2.3.6 3.6.6.6 0 1 .4 1 1V20c0 .6-.4 1-1 1A17 17 0 013 4c0-.6.4-1 1-1h3.5c.6 0 1 .4 1 1 0 1.3.2 2.5.6 3.6.1.3 0 .7-.2 1z" fill="#fff"/></svg></div><div>Phone<br>123-456-7890</div></div>
</footer>

<div class="band bottombar">
  <div class="abs" style="left:141px;top:15px">©2024 Harvest Crest Oruva. All Rights Reserved.</div>
  <div class="social"><span></span><span></span><span></span><span></span></div>
</div>

</body>
</html>
```